strength and conditioning business focused on helping people move more efficiently

I need a business card designed for a Philadelphia based company called Brsk Lft Motion (pronounced Brisk Lift). We offer fitness professional services with the idea of helping people feel better and move optimally. We do this by designing and walking through individualized programs as well as minor soft tissue work. Our perfect client would be athletes but we will be marketing to parents who have children that are active They remember their former athletic days and want to get as close as possible back to that feeling. Attached will be the official logo and logo formats. I would love for the design to communicate trustworthy and creative. I would also love for the design to be square with rounded edges.

Target Market(s)

Parents of athletic children
former athletes
athletes

Industry/Entity Type

Fitness

Contact Information for Business Card

Business: Brsk Lft Performance
Name: Coach Calvin Ashworth
Position: Strength and Conditioning Coach / Certified Personal Trainer
Contact: coach.ash@brsklft.com
Text: (555)204-7781

Font styles to use
Serif
Sans Serif

Colors
fbee38
fbee3e
0255a3
3176b5
ffffff

Requirements
Must have
• use of logo
Nice to have
• Square design
rounded edges

```html
<!DOCTYPE html>
<html lang="en">
<head>
<meta charset="utf-8">
<title>Brsk Lft Motion – Business Card</title>
<link rel="stylesheet" href="https://fonts.googleapis.com/css2?family=Open+Sans:wght@400;700;800&family=Arimo:wght@400&display=swap">
<style>
  :root {
    --navy: #0a286c;
    --gold: #f2c12e;
    --white: #ffffff;
    --paper: #f7f7f6;
    --ink: #2a2a2a;
    --backdrop: #dadada;
  }
  html, body {
    margin: 0;
    padding: 0;
    width: 1200px;
    height: 908px;
    overflow: hidden;
    background: var(--backdrop);
  }
  .canvas {
    position: relative;
    width: 1200px;
    height: 908px;
  }
  .card {
    position: absolute;
    top: 224px;
    width: 460px;
    height: 460px;
    border-radius: 44px;
    box-shadow: 0 6px 18px rgba(0,0,0,0.18);
    box-sizing: border-box;
  }
  .card-front {
    left: 80px;
    background: var(--navy);
    display: flex;
    align-items: center;
    justify-content: center;
  }
  .brand {
    display: flex;
    align-items: center;
    gap: 14px;
  }
  .brand-dot {
    width: 40px;
    height: 40px;
    border-radius: 50%;
    background: var(--gold);
    flex: none;
  }
  .brand-name {
    font-family: "Open Sans", sans-serif;
    font-weight: 800;
    font-size: 46px;
    letter-spacing: -0.5px;
    color: var(--white);
    white-space: nowrap;
  }
  .card-back {
    left: 660px;
    background: var(--paper);
    padding: 0 34px;
    display: flex;
    flex-direction: column;
    justify-content: center;
  }
  .coach-name {
    font-family: "Open Sans", sans-serif;
    font-weight: 800;
    font-size: 24px;
    letter-spacing: 3.5px;
    color: var(--navy);
    margin: 0;
    white-space: nowrap;
  }
  .rule {
    height: 2px;
    background: var(--gold);
    margin: 8px 0;
  }
  .coach-title {
    font-family: "Arimo", sans-serif;
    font-size: 13.5px;
    color: var(--ink);
    margin: 0;
    white-space: nowrap;
  }
  .contacts {
    display: flex;
    gap: 10px;
    font-family: "Arimo", sans-serif;
    font-size: 12px;
    color: var(--ink);
    white-space: nowrap;
  }
  .contact {
    display: flex;
    align-items: center;
    gap: 4px;
  }
  .contact svg { width: 12px; height: 12px; flex: none; }
</style>
</head>
<body>
<main class="canvas">
  <section class="card card-front" aria-label="Card front">
    <div class="brand">
      <span class="brand-dot"></span>
      <span class="brand-name">Brsk Lft Motion</span>
    </div>
  </section>

  <section class="card card-back" aria-label="Card back">
    <h1 class="coach-name">COACH CALVIN ASHWORTH</h1>
    <div class="rule"></div>
    <p class="coach-title">Strength and Conditioning Coach / Certified Personal Trainer</p>
    <div class="rule"></div>
    <div class="contacts">
      <span class="contact">
        <svg viewBox="0 0 12 12" aria-hidden="true"><circle cx="6" cy="6" r="6" fill="#0a286c"/><path d="M4 3.2l1 1.3-.6.7c.4.8 1 1.4 1.8 1.8l.7-.6 1.3 1-.6 1c-2.2-.3-4-2.1-4.3-4.3z" fill="#fff"/></svg>
        (555)204-7781
      </span>
      <span class="contact">
        <svg viewBox="0 0 12 12" aria-hidden="true"><rect x="0.5" y="2" width="11" height="8" rx="1" fill="#0a286c"/><path d="M1 2.7l5 4 5-4" stroke="#fff" stroke-width="1" fill="none"/></svg>
        coach.ash@brsklft.com
      </span>
      <span class="contact">
        <svg viewBox="0 0 12 12" aria-hidden="true"><circle cx="6" cy="6" r="5.5" fill="#0a286c"/><ellipse cx="6" cy="6" rx="2.3" ry="5.5" stroke="#fff" stroke-width=".8" fill="none"/><path d="M0.5 6h11" stroke="#fff" stroke-width=".8"/></svg>
        www.brsklft.com
      </span>
    </div>
  </section>
</main>
</body>
</html>
```